Redesign of Form/Document Navigation Page

I need a redesign of our document and navigation bar on the left. We want the same navigation bar layout/setup but want the buttons and typography to be simple and matching all over. The form needs to be aesthetically pleasing and fit within the page.

1st attachment is our Direct Deposit and the second is the form continued.

```html
<!DOCTYPE html>
<html lang="en">
<head>
<meta charset="utf-8">
<title>Employee Direct Deposit Enrollment</title>
<link rel="stylesheet" href="https://fonts.googleapis.com/css2?family=Lato:wght@400;700;900&display=swap">
<style>
:root{
  --accent:#eab020;
  --accent-dark:#e0a515;
  --blue:#2e7bc4;
  --ink:#222;
  --text:#3a3a3a;
  --line:#d6d6d6;
  --soft-line:#e6e6e6;
  --page:#f3f3f3;
  --white:#fff;
  --track:#e8e8e8;
  --thumb:#cfcfcf;
}
*{box-sizing:border-box;margin:0;padding:0}
html,body{width:1200px;height:934px;overflow:hidden}
body{font-family:"Lato",sans-serif;color:var(--text);background:var(--page);position:relative}

.site-header{position:absolute;left:3px;top:0;width:1197px;height:80px;background:var(--white);box-shadow:0 1px 2px rgba(0,0,0,.05)}
.brand{position:absolute;left:80px;top:19px;display:flex;align-items:center;gap:8px}
.brand-mark{width:36px;height:36px;border-radius:50%;background:var(--blue)}
.brand-name{font-weight:900;font-size:19px;line-height:19px;color:var(--accent);text-transform:uppercase;letter-spacing:-.2px}
.top-nav{position:absolute;left:369px;top:30px;display:flex;gap:38px}
.top-nav a{display:flex;align-items:center;gap:8px;font-size:13px;color:var(--ink);text-decoration:none}
.user-btn{position:absolute;left:1011px;top:21px;width:105px;height:35px;border:1px solid var(--line);display:flex;align-items:center;justify-content:center;gap:8px;font-size:11px;color:var(--ink);background:var(--white)}

.back-btn{position:absolute;left:82px;top:94px;width:139px;height:38px;background:var(--blue);color:var(--white);font-weight:700;font-size:12.5px;display:flex;align-items:center;gap:12px;padding-left:18px}

.panel{position:absolute;left:82px;top:148px;width:1036px;height:678px;background:var(--white);border:1px solid var(--soft-line);overflow:hidden}
.side-nav{position:absolute;left:0;top:0;width:250px;height:100%;border-right:1px solid var(--soft-line)}
.side-item{display:flex;align-items:center;gap:18px;padding-left:30px;border-bottom:1px solid var(--soft-line);font-size:13.5px;color:var(--ink)}
.side-item svg{width:18px;height:18px;flex:none}
.side-item.active{border-left:3px solid var(--accent);padding-left:27px;color:var(--accent);font-weight:700}
.side-item:last-child{border-bottom:none}

.scrollbar{position:absolute;right:0;top:0;width:16px;height:100%;background:var(--track)}
.scrollbar .thumb{position:absolute;left:0;top:16px;width:16px;height:272px;background:var(--thumb)}
.scrollbar .arrow{position:absolute;left:0;width:16px;height:16px;background:#c8c8c8;display:flex;align-items:center;justify-content:center}

.form{position:absolute;left:288px;top:0;width:720px;height:100%}
.form-title{position:absolute;left:0;top:25px;font-size:19px;font-weight:700;color:var(--accent)}
.form p{position:absolute;font-size:11.4px;line-height:17.6px;color:var(--text)}
.attach-box{position:absolute;left:3px;top:177px;width:539px;height:66px;border:1px solid var(--soft-line);display:flex;align-items:center;padding-left:26px;font-size:12.5px;color:var(--ink)}
.refresh-btn{position:absolute;left:397px;top:12px;width:124px;height:39px;background:var(--accent);color:var(--white);font-weight:700;font-size:15.5px;display:flex;align-items:center;justify-content:center;gap:12px}
.section-head{position:absolute;font-size:11.5px;font-weight:700;color:var(--ink)}
.radio-row{position:absolute;display:flex;align-items:center;font-size:12px;color:var(--ink)}
.radio{width:12px;height:12px;border:1px solid #aaa;border-radius:50%;display:inline-block;margin-right:9px}
.field{position:absolute;height:41px;border:1px solid var(--line);font-size:12px;color:var(--ink);display:flex;align-items:center;padding-left:17px;width:207px}
.label{position:absolute;font-size:12px;color:var(--ink)}
</style>
</head>
<body>
<header class="site-header">
  <div class="brand"><span class="brand-mark"></span><span class="brand-name">Harborline<br>Security Services</span></div>
  <nav class="top-nav">
    <a href="#"><svg width="15" height="14" viewBox="0 0 15 14"><path d="M7.5 0 0 6.5h2V14h4V9.5h3V14h4V6.5h2z" fill="#222"/></svg>Home</a>
    <a href="#"><svg width="16" height="16" viewBox="0 0 16 16"><circle cx="8" cy="8" r="7" fill="none" stroke="#222" stroke-width="1.5"/><path d="M6 6.2a2 2 0 1 1 2.8 1.8c-.6.3-.8.7-.8 1.4" fill="none" stroke="#222" stroke-width="1.4"/><circle cx="8" cy="11.8" r=".9" fill="#222"/></svg>Help</a>
  </nav>
  <div class="user-btn"><svg width="15" height="15" viewBox="0 0 16 16"><path d="M4.5 3.5a6 6 0 1 0 7 0" fill="none" stroke="#eab020" stroke-width="1.6"/><path d="M8 1v6" stroke="#eab020" stroke-width="1.6"/></svg>Dana Whitfield</div>
</header>

<div class="back-btn"><svg width="8" height="11" viewBox="0 0 8 11"><path d="M6.5 1 2 5.5 6.5 10" fill="none" stroke="#fff" stroke-width="1.8"/></svg>Back to Profile</div>

<main class="panel">
  <nav class="side-nav">
    <div class="side-item active" style="height:98px"><svg viewBox="0 0 18 18"><rect x="1" y="3" width="16" height="12" rx="1" fill="none" stroke="#eab020" stroke-width="1.6"/><rect x="1" y="6" width="16" height="2" fill="#eab020"/></svg>Direct Deposit</div>
    <div class="side-item" style="height:96px"><svg viewBox="0 0 18 18"><circle cx="9" cy="10" r="7.5" fill="none" stroke="#333" stroke-width="1.4"/><circle cx="9" cy="10" r="4.3" fill="none" stroke="#333" stroke-width="1.4"/><circle cx="9" cy="10" r="1.5" fill="#333"/><path d="M9 10 6 1" stroke="#333" stroke-width="1.4"/></svg>Change W-4</div>
    <div class="side-item" style="height:94px"><svg viewBox="0 0 18 18"><g fill="#333"><rect x="1" y="1" width="2" height="2"/><rect x="5.3" y="1" width="2" height="2"/><rect x="9.6" y="1" width="2" height="2"/><rect x="14" y="1" width="2" height="2"/><rect x="1" y="5.3" width="2" height="2"/><rect x="14" y="5.3" width="2" height="2"/><rect x="1" y="9.6" width="2" height="2"/><rect x="14" y="9.6" width="2" height="2"/><rect x="1" y="14" width="2" height="2"/><rect x="5.3" y="14" width="2" height="2"/><rect x="9.6" y="14" width="2" height="2"/><rect x="14" y="14" width="2" height="2"/></g></svg>Labour Code</div>
    <div class="side-item" style="height:94px"><svg viewBox="0 0 18 18"><circle cx="9" cy="5" r="3.6" fill="#111"/><path d="M2 16c0-4 3.5-5.5 7-5.5s7 1.5 7 5.5z" fill="#111"/></svg>Personal Information</div>
    <div class="side-item" style="height:96px"><svg viewBox="0 0 18 18"><path d="M9 1l2.4 5.3 5.6.5-4.3 3.8 1.3 5.6L9 13.3l-5 2.9 1.3-5.6L1 6.8l5.6-.5z" fill="#111"/></svg>Appraisal and Review</div>
    <div class="side-item" style="height:95px"><svg viewBox="0 0 18 18"><path d="M2 13.5V16h2.5l9-9L11 4.5z" fill="#333"/><path d="M12.2 3.3l2.5 2.5 1.5-1.5-2.5-2.5z" fill="#333"/></svg>Write Up-Slip</div>
    <div class="side-item" style="height:105px"><svg viewBox="0 0 18 18"><path d="M1 14l5-5 3.5 3.5L17 5" fill="none" stroke="#111" stroke-width="1.8"/></svg>Employee Performance</div>
  </nav>

  <section class="form">
    <h1 class="form-title">Employee Direct Deposit Enrollment Form</h1>
    <p style="left:2px;top:65px;width:712px">To enroll in Direct Deposit, simply fill out this form. Attach a voided check for each checking account - not a deposit slip. If depositing to a savings account, ask your bank to give you the Routing/Transit Number for your account. It isn't always the same as the number on a savings deposit slip. This will help ensure that you are paid correctly. Once filled out, accounting will review your information for processing. Once processed, you will receive an email confirmation with details.</p>
    <p style="left:3px;top:145px;width:712px">Employees must attach a voided check for each of their accounts to help verify their account numbers and bank routing numbers.</p>

    <div class="attach-box">Attach A Voided Check Or Bank Deposit Form for the Account
      <div class="refresh-btn"><svg width="17" height="15" viewBox="0 0 17 15"><path d="M2.5 6.5A6 6 0 0 1 13.5 4" fill="none" stroke="#fff" stroke-width="1.7"/><path d="M14.5 8.5A6 6 0 0 1 3.5 11" fill="none" stroke="#fff" stroke-width="1.7"/><path d="M14.5 1v4h-4M2.5 14v-4h4" fill="none" stroke="#fff" stroke-width="1.7"/></svg>Refresh</div>
    </div>

    <div class="section-head" style="left:5px;top:266px">Account Information</div>
    <p style="left:5px;top:285px;width:712px">The last item must be for the remaining amount owed to you. To distribute to more accounts, please complete another form. Make sure to indicate what kind of account, along with enrolling or declining.</p>

    <div class="section-head" style="left:2px;top:343px;font-size:12px">**NOTIFY PAYROLL IMMEDIATELY IF YOU CLOSE OR CHANGE BANK ACCOUNT**</div>
    <div class="radio-row" style="left:6px;top:366px"><span class="radio"></span>New Enrollment<span class="radio" style="margin-left:13px"></span>Change Enrollment<span class="radio" style="margin-left:13px"></span>Cancel Enrollment</div>

    <div class="field" style="left:9px;top:405px">Bank Name</div>
    <div class="field" style="left:234px;top:405px">City</div>
    <div class="field" style="left:461px;top:405px">State</div>

    <div class="field" style="left:9px;top:460px">Routing Transit #</div>
    <div class="field" style="left:237px;top:460px">Account Number.</div>
    <div class="radio-row" style="left:463px;top:474px"><span class="radio"></span>Checking<span class="radio" style="margin-left:38px"></span>Savings</div>

    <div class="label" style="left:11px;top:529px">Amount</div>
    <div class="field" style="left:70px;top:515px;width:126px;padding-left:13px">100</div>
    <div class="label" style="left:206px;top:529px;font-size:11px">%</div>

    <div class="section-head" style="left:1px;top:584px">IMPORTANT! Please read and sign before completing and submitting.</div>
    <p style="left:2px;top:603px;width:712px">I hereby authorize HARBORLINE SECURITY SERVICES to deposit any amounts owed me, as instructed by my employer, by initiating credit entries to my account at the financial institution (hereinafter "Bank") indicated on this form. Further, I authorize Bank to accept and to credit any credit entries indicated by HARBORLINE</p>
  </section>

  <div class="scrollbar">
    <div class="arrow" style="top:0"><svg width="8" height="5" viewBox="0 0 8 5"><path d="M1 4.5 4 1.5l3 3" fill="none" stroke="#fff" stroke-width="1.3"/></svg></div>
    <div class="thumb"></div>
    <div class="arrow" style="bottom:0"><svg width="8" height="5" viewBox="0 0 8 5"><path d="M1 .5 4 3.5l3-3" fill="none" stroke="#fff" stroke-width="1.3"/></svg></div>
  </div>
</main>

<footer style="position:absolute;left:0;top:870px;width:1200px;height:64px;background:var(--white);text-align:center;font-size:11px;color:var(--ink);padding-top:25px">Copyrights @ 2016 All Rights Reserved</footer>
</body>
</html>
```